Business Card Design

New business card design

Target Market(s)

Residential & Commercial Property Managers

Industry/Entity Type

Plumbing Services

Contact Information for Business Card

Name - Rowan Keddle, title - Director, Phone Number - 0431 286 517, email - rowan@tbk-plumbing.com.au, Company ABN - 73 215 904 386,

Font styles to use
Sans Serif

Colors
0054AA
0677BA
7BADD7
CADEEF
E8F1F8

```html
<!DOCTYPE html>
<html lang="en">
<head>
<meta charset="utf-8">
<title>TBK Plumbing Services – Business Card</title>
<link rel="stylesheet" href="https://fonts.googleapis.com/css2?family=Roboto:wght@300;700&display=swap">
<style>
  :root {
    --backdrop: #1d1e21;
    --blue-deep: #0a4c95;
    --blue-navy: #0054aa;
    --blue-mid: #0677ba;
    --blue-sky: #45addb;
    --blue-light: #7badd7;
    --blue-pale: #cadeef;
    --white: #ffffff;
    --text-soft: #e8f1f8;
  }
  * { box-sizing: border-box; margin: 0; padding: 0; }
  html, body { width: 1200px; height: 852px; overflow: hidden; }
  body {
    background: var(--backdrop);
    font-family: "Roboto", Arial, sans-serif;
    position: relative;
  }
  .card {
    position: absolute;
    top: 276px;
    width: 520px;
    height: 300px;
    border-radius: 22px;
    overflow: hidden;
    color: var(--white);
  }
  .card--front { left: 50px; }
  .card--back { left: 630px; }
  .card__backdrop {
    position: absolute;
    inset: 0;
    background: linear-gradient(170deg, var(--blue-sky) 0%, var(--blue-mid) 50%, var(--blue-deep) 100%);
  }

  .wordmark { position: absolute; text-align: center; }
  .wordmark__name {
    font-weight: 300;
    font-size: 120px;
    line-height: 1;
    letter-spacing: 2px;
    color: var(--white);
  }
  .wordmark__tagline {
    font-weight: 300;
    font-size: 13px;
    letter-spacing: 9px;
    color: var(--blue-pale);
    margin-top: 4px;
  }
  .card--front .wordmark { left: 0; right: 0; top: 70px; }

  .card--back .wordmark {
    right: -52px;
    top: 92px;
    width: 240px;
    transform: rotate(90deg);
  }
  .card--back .wordmark__name { font-size: 92px; }
  .card--back .wordmark__tagline { font-size: 10px; letter-spacing: 7px; }

  .holder { position: absolute; left: 30px; top: 34px; }
  .holder__name { font-weight: 700; font-size: 21px; letter-spacing: -0.3px; }
  .holder__title { font-weight: 300; font-size: 14px; color: var(--blue-pale); margin-top: 2px; }

  .contact { position: absolute; left: 30px; bottom: 26px; font-weight: 300; font-size: 13px; }
  .contact__location { margin-bottom: 10px; color: var(--text-soft); }
  .contact__list { list-style: none; }
  .contact__item { display: flex; align-items: center; gap: 10px; line-height: 20px; color: var(--text-soft); }
  .contact__icon { width: 13px; height: 13px; flex: none; }
</style>
</head>
<body>

<section class="card card--front" aria-label="Card front">
  <div class="card__backdrop" role="img" aria-label="Layered blue water-wave background"></div>
  <div class="wordmark">
    <div class="wordmark__name">tbk</div>
    <div class="wordmark__tagline">plumbing services</div>
  </div>
</section>

<section class="card card--back" aria-label="Card back">
  <div class="card__backdrop" role="img" aria-label="Layered blue water-wave background"></div>

  <div class="holder">
    <div class="holder__name">Rowan Keddle</div>
    <div class="holder__title">Director</div>
  </div>

  <div class="contact">
    <p class="contact__location">Sydney &nbsp;|&nbsp; NSW &nbsp;|&nbsp; Australia</p>
    <ul class="contact__list">
      <li class="contact__item">
        <svg class="contact__icon" viewBox="0 0 16 16" aria-hidden="true"><path d="M4 1 L6.5 4.5 L5 6.5 C6 8.5 7.5 10 9.5 11 L11.5 9.5 L15 12 L13.5 15 C7 14.5 1.5 9 1 2.5Z" fill="#7badd7"/></svg>
        <span>0431 286 517</span>
      </li>
      <li class="contact__item">
        <svg class="contact__icon" viewBox="0 0 16 16" aria-hidden="true"><rect x="1" y="3" width="14" height="10" fill="#7badd7"/><path d="M1 3 L8 9 L15 3" fill="none" stroke="#0a4f98" stroke-width="1.3"/></svg>
        <span>rowan@tbk-plumbing.com.au</span>
      </li>
      <li class="contact__item">
        <svg class="contact__icon" viewBox="0 0 16 16" aria-hidden="true"><circle cx="8" cy="8" r="6.5" fill="#7badd7"/><path d="M1.5 8 H14.5 M8 1.5 C5 5 5 11 8 14.5 M8 1.5 C11 5 11 11 8 14.5" fill="none" stroke="#0a4f98" stroke-width="1"/></svg>
        <span>www.tbk-plumbing.com.au</span>
      </li>
      <li class="contact__item">
        <svg class="contact__icon" viewBox="0 0 16 16" aria-hidden="true"><path d="M6 1 L4.5 15 M11.5 1 L10 15 M2 5.5 H15 M1 10.5 H14" stroke="#7badd7" stroke-width="1.8" fill="none"/></svg>
        <span>ABN - 73 215 904 386</span>
      </li>
    </ul>
  </div>

  <div class="wordmark">
    <div class="wordmark__name">tbk</div>
    <div class="wordmark__tagline">plumbing services</div>
  </div>
</section>

</body>
</html>
```